Create a memorable Stationary for Security Software Company

Velbrantix is the worldwide leader in securing the Internet. Making Internet communications and critical data secure, reliable and available everywhere has been and continues to be our ongoing vision. We are committed to staying focused on real customer needs and to developing new and innovative security solutions that redefine the security landscape.

Industry/Entity Type

Internet

Font styles to use
Serif
Sans Serif
Script

Colors
0792cd
33a6d7
85cae6

```html
<!DOCTYPE html>
<html lang="en">
<head>
<meta charset="utf-8">
<title>Velbrantix Stationery</title>
<link href="https://fonts.googleapis.com/css2?family=Questrial&display=swap" rel="stylesheet">
<style>
:root{
  --blue-deep:#0792cd;
  --blue-mid:#33a6d7;
  --blue-soft:#85cae6;
  --blue-fill:#1ea3da;
  --paper:#ffffff;
  --sheet:#eef0f1;
  --stage:#e9eaec;
  --ink:#222222;
}
*{box-sizing:border-box;margin:0;padding:0}
html,body{width:1200px;height:1043px;overflow:hidden}
body{background:var(--stage);font-family:"Questrial",sans-serif;position:relative}
.piece{position:absolute;overflow:hidden;box-shadow:0 3px 10px rgba(0,0,0,.18)}
.cloud-band{position:absolute;left:0;width:100%}
.brand{display:flex;align-items:center;gap:10px;color:var(--blue-deep)}
.brand-dot{border-radius:50%;background:var(--blue-deep);flex:none}
.brand-name{font-weight:400;letter-spacing:.5px}

/* folder cover */
.folder{left:60px;top:60px;width:490px;height:640px;background:var(--blue-soft)}
.folder .cloud-band.top{top:0;height:170px;background:linear-gradient(var(--blue-fill),var(--blue-mid))}
.folder .cloud-band.bottom{bottom:0;height:150px;background:linear-gradient(var(--blue-mid),var(--blue-fill))}
.folder .brand{position:absolute;left:0;right:0;top:300px;justify-content:center}
.folder .brand-dot{width:34px;height:34px}
.folder .brand-name{font-size:40px}
.folder .site{position:absolute;left:0;right:0;top:370px;text-align:center;color:var(--blue-deep);font-size:17px;letter-spacing:.5px}

/* letterhead */
.letterhead{left:630px;top:60px;width:480px;height:600px;background:var(--sheet)}
.letterhead .cloud-band.top{top:0;height:60px;background:linear-gradient(var(--paper),var(--sheet))}
.letterhead .brand{position:absolute;left:40px;top:40px}
.letterhead .brand-dot{width:18px;height:18px}
.letterhead .brand-name{font-size:17px}
.letterhead .title{position:absolute;left:45px;top:150px;font-size:9px;font-weight:700;color:var(--ink);font-family:"Questrial",sans-serif}
.letterhead .body{position:absolute;left:45px;top:178px;width:370px;font-size:7.4px;line-height:1.25;color:var(--ink)}
.letterhead .body p{margin-bottom:9px}
.letterhead .cloud-band.pocket{bottom:0;left:90px;width:390px;height:250px;background:var(--blue-fill);border-top-left-radius:170px 130px;border-top-right-radius:60px 80px}

/* business cards */
.card{left:57px;width:192px;height:106px}
.card.front{top:755px;background:var(--paper)}
.card.front .brand{position:absolute;left:0;right:0;top:38px;justify-content:center}
.card.front .brand-dot{width:12px;height:12px}
.card.front .brand-name{font-size:15px}
.card.front .site{position:absolute;left:0;right:0;top:78px;text-align:center;font-size:7px;color:var(--blue-deep);font-weight:700}
.card.back{top:892px;background:var(--blue-soft)}
.card.back .cloud-band.top{top:0;height:24px;background:var(--blue-fill)}
.card.back .cloud-band.bottom{bottom:0;height:14px;background:var(--blue-fill)}
.card.back .brand{position:absolute;left:0;right:0;top:6px;justify-content:center;color:var(--blue-soft)}
.card.back .brand-dot{width:9px;height:9px;background:var(--blue-soft)}
.card.back .brand-name{font-size:12px}
.card.back .details{position:absolute;left:0;right:0;top:40px;text-align:center;color:var(--blue-deep);font-size:5.4px;line-height:1.4}
.card.back .details .name{font-weight:700;letter-spacing:.4px}

/* DL envelope, address side */
.envelope{left:290px;top:745px;width:360px;height:230px;background:var(--blue-mid)}
.envelope .cloud-band.left{left:0;top:60px;width:170px;height:170px;background:var(--blue-soft);border-top-right-radius:90px}
.envelope .brand{position:absolute;left:22px;top:120px}
.envelope .brand-dot{width:12px;height:12px}
.envelope .brand-name{font-size:15px}
.envelope .details{position:absolute;left:22px;top:160px;font-size:6.5px;line-height:1.4;color:var(--blue-deep)}

/* envelope, flap side */
.env-back{left:672px;top:690px;width:474px;height:305px;background:var(--blue-mid)}
.env-back .flap{position:absolute;left:0;top:0;width:100%;height:80px;background:var(--paper);border-radius:14px 14px 0 0}
.env-back .cloud-band.bottom{bottom:0;height:80px;background:linear-gradient(var(--blue-mid),var(--blue-fill))}
.env-back .brand{position:absolute;left:24px;top:228px;color:var(--blue-soft)}
.env-back .brand-dot{width:12px;height:12px;background:var(--blue-soft)}
.env-back .brand-name{font-size:14px}
.env-back .details{position:absolute;right:26px;top:245px;text-align:right;font-size:6.5px;line-height:1.5;color:var(--blue-soft)}
</style>
</head>
<body>

<section class="piece folder">
  <div class="cloud-band top" role="img" aria-label="Band of stylised deep blue clouds"></div>
  <div class="brand"><span class="brand-dot"></span><span class="brand-name">Velbrantix</span></div>
  <div class="site">velbrantix.com</div>
  <div class="cloud-band bottom" role="img" aria-label="Band of stylised deep blue clouds"></div>
</section>

<section class="piece letterhead">
  <div class="cloud-band top" role="img" aria-label="Outlined white clouds along the top edge"></div>
  <div class="brand"><span class="brand-dot"></span><span class="brand-name">Velbrantix</span></div>
  <div class="title">Lorem Ipsum</div>
  <div class="body">
    <p>Lorem ipsum dolor sit amet, consectetur adipiscing elit. Proin non posuere nisl. Ut fringilla sapien nisi. Nunc ac feugiat erat. Proin vel arcu sed odio posuere hendrerit. Sed viverra purus erat, vitae volutpat nulla dapibus sed. Mauris a leo vitae lorem tempus iaculis ac in diam. Mauris venenatis vitae metus vitae volutpat. Aliquam erat volutpat. Praesent aliquam diam vel odio hendrerit, a efficitur dui sollicitudin. Nulla varius diam et pellentesque tincidunt. Sed faucibus eu massa quis venenatis. Suspendisse turpis libero, viverra sed aliquam quis, pulvinar non ligula. Integer viverra, nulla vitae egestas blandit, mauris ante commodo arcu, eu bibendum mauris tellus pulvinar orci. Proin ipsum nisi, consequat non finibus tristique, malesuada a velit.</p>
    <p>Proin rhoncus nunc vitae massa fermentum, in tempus nisi tempor. Donec nec efficitur augue. Mauris sagittis eleifend nulla sit amet sodales. Donec ultricies tempor nunc id convallis. Integer libero sem, varius nec nisi vitae, consectetur facilisis orci. Vestibulum non tortor varius, auctor nunc at, maximus metus. In non augue at nibh eleifend maximus. Sed suscipit congue ipsum, eu aliquet diam volutpat at. Integer sed venenatis augue, vel vulputate massa.</p>
    <p>Suspendisse potenti. Sed at sapien sit amet dolor luctus lacinia a ut ligula. Nulla nec magna condimentum, placerat neque a, vestibulum orci. Sed tristique quam quis sapien efficitur mollis. Morbi fringilla magna quam, ac hendrerit turpis dapibus non. Sed id finibus massa.</p>
  </div>
  <div class="cloud-band pocket" role="img" aria-label="Cloud-shaped blue folder pocket"></div>
</section>

<section class="piece card front">
  <div class="brand"><span class="brand-dot"></span><span class="brand-name">Velbrantix</span></div>
  <div class="site">velbrantix.com</div>
</section>

<section class="piece card back">
  <div class="cloud-band top" role="img" aria-label="Blue cloud band"></div>
  <div class="brand"><span class="brand-dot"></span><span class="brand-name">Velbrantix</span></div>
  <div class="details">
    <div class="name">NAME OF SOMEBODY</div>
    <div>Director</div>
    <div style="margin-top:6px">55 3555.0147 &nbsp;|&nbsp; 55 3556.0389</div>
    <div>418 Harlow Av | Dunmere, CO 80519</div>
  </div>
  <div class="cloud-band bottom" role="img" aria-label="Blue cloud band"></div>
</section>

<section class="piece envelope">
  <div class="cloud-band left" role="img" aria-label="Large pale blue cloud"></div>
  <div class="brand"><span class="brand-dot"></span><span class="brand-name">Velbrantix</span></div>
  <div class="details">418 Harlow Av<br>Dunmere, CO 80519<br>55 3555.0147 | 55 3556.0389</div>
</section>

<section class="piece env-back">
  <div class="flap" role="img" aria-label="White envelope flap with outlined clouds"></div>
  <div class="cloud-band bottom" role="img" aria-label="Band of stylised blue clouds"></div>
  <div class="brand"><span class="brand-dot"></span><span class="brand-name">Velbrantix</span></div>
  <div class="details">Name of Somebody<br>418 Harlow Av | Dunmere, CO 80519</div>
</section>

</body>
</html>
```